SOLVE Study flyer

I need help designing a flyer for a research study that will include brain imaging in adolescents. The info is in the attached document. The study is called the Sequoia Outlook Lantern Valley Echo (SOLVE) study. Ideally this would be returned as a document that I can edit in the future as we will have several new recruitment phases (different age groups, etc. I also would love to have a logo designed as part of this project, but I recognize that might be a separate design request.

```html
<!DOCTYPE html>
<html lang="en">
<head>
<meta charset="utf-8">
<title>SOLVE Study Recruitment Flyer</title>
<link rel="stylesheet" href="https://fonts.googleapis.com/css2?family=Poppins:wght@500;600;700;800&family=Open+Sans:wght@400;600;700&family=Oswald:wght@500;600&display=swap">
<style>
  :root {
    --navy: #0f1a3a;
    --ink: #1d1d1f;
    --purple: #5a3a9e;
    --teal: #12a89d;
    --sky: #1aa9e8;
    --gold: #f9bf1a;
    --paper: #ffffff;
    --mist: #f1f1f0;
    --text: #2b2b2b;
  }
  * { box-sizing: border-box; margin: 0; padding: 0; }
  html, body { width: 950px; height: 1200px; overflow: hidden; background: var(--paper); }
  .flyer { position: relative; width: 950px; height: 1200px; background: var(--paper); font-family: "Open Sans", sans-serif; color: var(--text); }

  .hero { position: absolute; left: 0; top: 0; width: 950px; height: 511px;
    background: linear-gradient(90deg, #ffffff 0%, #f6f6f5 30%, var(--mist) 100%); }
  .hero-visual { position: absolute; left: 429px; top: 0; width: 521px; height: 511px;
    background:
      radial-gradient(ellipse 45% 55% at 78% 42%, rgba(246,196,40,.75), rgba(236,72,60,.45) 45%, rgba(120,70,190,.25) 70%, transparent 85%),
      radial-gradient(ellipse 40% 50% at 40% 55%, rgba(200,190,180,.55), transparent 80%),
      linear-gradient(90deg, #f3f3f2 0%, #e8e6e3 100%); }

  .brand { position: absolute; left: 91px; top: 62px; display: flex; align-items: center; gap: 10px; }
  .brand-mark { width: 34px; height: 34px; background: var(--navy); }
  .brand-name { font-family: "Poppins", sans-serif; font-weight: 600; font-size: 17px; line-height: 1.1; color: var(--navy); }

  .headline { position: absolute; left: 73px; top: 130px; font-family: "Poppins", sans-serif; font-weight: 800;
    font-size: 46px; line-height: 59px; color: var(--ink); letter-spacing: -0.5px; }
  .headline .accent { color: var(--purple); }
  .headline-rule { position: absolute; left: 78px; top: 328px; width: 98px; height: 5px; background: var(--gold); }
  .subhead { position: absolute; left: 76px; top: 360px; font-family: "Poppins", sans-serif; font-weight: 700;
    font-size: 28px; line-height: 36px; color: var(--ink); letter-spacing: -0.3px; }

  .intro { position: absolute; left: 65px; top: 491px; width: 819px; height: 177px; background: var(--navy);
    border-radius: 14px; }
  .intro-icon { position: absolute; left: 33px; top: 10px; width: 170px; height: 160px; }
  .intro-text { position: absolute; left: 247px; top: 32px; width: 520px; font-family: "Poppins", sans-serif;
    font-weight: 500; font-size: 15.3px; line-height: 26px; color: #fff; }

  .section-title { font-family: "Poppins", sans-serif; font-weight: 800; font-size: 22px; line-height: 27px; letter-spacing: -0.2px; }
  .participation { position: absolute; left: 95px; top: 676px; width: 400px; }
  .participation .section-title { color: var(--purple); }
  .steps { position: absolute; left: 0; top: 0; }
  .step { position: absolute; left: 0; width: 400px; }
  .step-icon { position: absolute; left: 8px; width: 50px; height: 50px; border-radius: 50%; }
  .step-icon svg { width: 50px; height: 50px; }
  .step-text { position: absolute; left: 84px; width: 320px; font-size: 15.5px; line-height: 22px; }
  .step-text strong { font-weight: 700; color: var(--ink); }
  .teal-bg { background: var(--teal); }
  .purple-bg { background: var(--purple); }
  .sky-bg { background: var(--sky); }

  .eligibility { position: absolute; left: 548px; top: 679px; width: 320px; }
  .eligibility .line-a { color: var(--teal); }
  .eligibility .line-b { color: var(--navy); }
  .criteria { list-style: none; }
  .criterion { position: absolute; left: 0; width: 320px; }
  .criterion-tick { position: absolute; left: 3px; width: 28px; height: 28px; }
  .criterion-text { position: absolute; left: 51px; width: 260px; font-weight: 600; font-size: 19px; line-height: 26px; color: var(--ink); }
  .criterion-divider { position: absolute; left: 51px; width: 241px; height: 1px; background: var(--teal); }

  .footer { position: absolute; left: 0; top: 1047px; width: 950px; height: 153px; background: var(--navy); }
  .cta-title { position: absolute; left: 88px; top: 20px; font-family: "Oswald", sans-serif; font-weight: 600;
    font-size: 26px; line-height: 32px; color: #fff; letter-spacing: 0.2px; }
  .cta-note { position: absolute; left: 89px; top: 55px; font-family: "Poppins", sans-serif; font-weight: 500; font-size: 12.5px; color: #fff; }
  .cta-email { position: absolute; left: 92px; top: 85px; width: 319px; height: 34px; background: var(--teal); border-radius: 4px;
    display: flex; align-items: center; padding-left: 12px; gap: 12px; font-family: "Poppins", sans-serif; font-weight: 500; font-size: 18px; color: #fff; }
  .footer-divider { position: absolute; left: 483px; top: 21px; width: 1px; height: 105px; background: rgba(255,255,255,.55); }
  .gift { position: absolute; left: 522px; top: 14px; width: 94px; height: 104px; }
  .comp-title { position: absolute; left: 641px; top: 20px; font-family: "Poppins", sans-serif; font-weight: 700; font-size: 24.5px; line-height: 32px; color: #fff; }
  .comp-upto { position: absolute; left: 643px; top: 60px; font-family: "Poppins", sans-serif; font-weight: 700; font-size: 20px; line-height: 22px; color: #fff; }
  .comp-amount { position: absolute; left: 688px; top: 44px; font-family: "Poppins", sans-serif; font-weight: 800; font-size: 64px; line-height: 74px; color: var(--gold); letter-spacing: -1px; }
</style>
</head>
<body>
<main class="flyer">
  <section class="hero">
    <div class="hero-visual" role="img" aria-label="Photo of a thoughtful teenage girl in front of a brain drawing, half covered in maths formulas and half in colourful paint splashes"></div>

    <div class="brand">
      <span class="brand-mark"></span>
      <span class="brand-name">Northvale<br>University</span>
    </div>

    <h1 class="headline">ARE YOU THE<br>PARENT OF A<br><span class="accent">CHILD AGE 10-17?</span></h1>
    <div class="headline-rule"></div>
    <h2 class="subhead">DO THEY WORRY OR<br>OVERTHINK NEGATIVE<br>EMOTIONS?</h2>
  </section>

  <section class="intro">
    <svg class="intro-icon" viewBox="0 0 170 160" aria-hidden="true">
      <g stroke="var(--gold)" stroke-width="3" stroke-linecap="round">
        <line x1="85" y1="6" x2="85" y2="22"/><line x1="85" y1="138" x2="85" y2="154"/>
        <line x1="12" y1="80" x2="30" y2="80"/><line x1="140" y1="80" x2="158" y2="80"/>
        <line x1="46" y1="14" x2="54" y2="28"/><line x1="124" y1="14" x2="116" y2="28"/>
        <line x1="46" y1="146" x2="54" y2="132"/><line x1="124" y1="146" x2="116" y2="132"/>
        <line x1="18" y1="42" x2="32" y2="50"/><line x1="152" y1="42" x2="138" y2="50"/>
        <line x1="18" y1="118" x2="32" y2="110"/><line x1="152" y1="118" x2="138" y2="110"/>
      </g>
      <g fill="none" stroke="#fff" stroke-width="3" stroke-linecap="round" stroke-linejoin="round">
        <path d="M83 40 C70 30 52 36 52 50 C40 54 38 72 46 80 C38 90 44 108 58 110 C62 122 78 124 83 114 Z"/>
        <path d="M87 40 C100 30 118 36 118 50 C130 54 132 72 124 80 C132 90 126 108 112 110 C108 122 92 124 87 114 Z"/>
        <path d="M64 58 C70 62 72 70 66 76 M60 94 C68 90 74 96 72 104 M106 58 C100 62 98 70 104 76 M110 94 C102 90 96 96 98 104"/>
      </g>
    </svg>
    <p class="intro-text">Northvale University researchers are seeking girls age 10-17 for a study about brain activity in emotions and decision-making and how they relate to puberty, anxiety and depression.</p>
  </section>

  <section class="participation">
    <h3 class="section-title">STUDY PARTICIPATION<br>INVOLVES:</h3>
    <div class="steps">
      <div class="step" style="top:97px">
        <div class="step-icon teal-bg" style="top:7px">
          <svg viewBox="0 0 50 50" aria-hidden="true"><g fill="none" stroke="#fff" stroke-width="1.6" stroke-linejoin="round"><rect x="16" y="20" width="18" height="12"/><path d="M13 35 H37"/><circle cx="25" cy="25" r="2.5"/><path d="M21 31 C21 28 29 28 29 31"/><path d="M22 15 C24 13 26 13 28 15 M23.5 17 C24.5 16 25.5 16 26.5 17"/></g></svg>
        </div>
        <p class="step-text"><strong>One one-hour interview</strong><br>(online or in-person) where your child will discuss their thoughts</p>
      </div>
      <div class="step" style="top:174px">
        <div class="step-icon purple-bg" style="top:3px">
          <svg viewBox="0 0 50 50" aria-hidden="true"><g fill="none" stroke="#fff" stroke-width="1.6"><rect x="17" y="14" width="16" height="22"/><path d="M20 19 H30 M20 23 H30 M20 27 H30 M20 31 H27"/></g></svg>
        </div>
        <p class="step-text"><strong>Online questionnaires</strong><br>(parent and child)</p>
      </div>
      <div class="step" style="top:230px">
        <div class="step-icon sky-bg" style="top:30px">
          <svg viewBox="0 0 50 50" aria-hidden="true"><g fill="none" stroke="#fff" stroke-width="1.6" stroke-linecap="round"><circle cx="25" cy="25" r="11"/><path d="M25 18 V25 L29 28"/></g></svg>
        </div>
        <p class="step-text"><strong>One two-hour visit</strong> where your child will complete an MRI scan, answer questions about their puberty stage, and have a small hair sample taken to study puberty hormones</p>
      </div>
    </div>
  </section>

  <section class="eligibility">
    <h3 class="section-title"><span class="line-a">YOUR CHILD MAY</span><br><span class="line-b">BE ELIGIBLE IF THEY:</span></h3>
    <ul class="criteria">
      <li class="criterion" style="top:104px">
        <svg class="criterion-tick" style="top:1px" viewBox="0 0 28 28" aria-hidden="true"><circle cx="14" cy="14" r="14" fill="var(--teal)"/><path d="M8.5 14.5 L12.5 18 L19.5 10" fill="none" stroke="#fff" stroke-width="2" stroke-linecap="round" stroke-linejoin="round"/></svg>
        <span class="criterion-text">Are age 10-17</span>
      </li>
      <li class="criterion-divider" style="top:147px"></li>
      <li class="criterion" style="top:164px">
        <svg class="criterion-tick" style="top:6px" viewBox="0 0 28 28" aria-hidden="true"><circle cx="14" cy="14" r="14" fill="var(--teal)"/><path d="M8.5 14.5 L12.5 18 L19.5 10" fill="none" stroke="#fff" stroke-width="2" stroke-linecap="round" stroke-linejoin="round"/></svg>
        <span class="criterion-text">Tend to worry or overthink negative thoughts</span>
      </li>
      <li class="criterion-divider" style="top:235px"></li>
      <li class="criterion" style="top:251px">
        <svg class="criterion-tick" style="top:5px" viewBox="0 0 28 28" aria-hidden="true"><circle cx="14" cy="14" r="14" fill="var(--teal)"/><path d="M8.5 14.5 L12.5 18 L19.5 10" fill="none" stroke="#fff" stroke-width="2" stroke-linecap="round" stroke-linejoin="round"/></svg>
        <span class="criterion-text">Have not been diagnosed with psychosis, learning problems, or autism</span>
      </li>
    </ul>
  </section>

  <footer class="footer">
    <p class="cta-title">INTERESTED IN PARTICIPATING?</p>
    <p class="cta-note">Want more information? Please contact us!</p>
    <p class="cta-email">
      <svg width="20" height="20" viewBox="0 0 20 20" aria-hidden="true"><circle cx="10" cy="10" r="10" fill="#fff"/><rect x="5" y="6.5" width="10" height="7" fill="var(--navy)"/><path d="M5 6.5 L10 10.5 L15 6.5" fill="none" stroke="#fff" stroke-width="1"/></svg>
      solvestudy@northvale.edu
    </p>
    <div class="footer-divider"></div>
    <svg class="gift" viewBox="0 0 94 104" aria-hidden="true">
      <g fill="none" stroke="var(--gold)" stroke-width="4" stroke-linejoin="round">
        <rect x="3" y="24" width="88" height="18"/>
        <rect x="8" y="42" width="78" height="59"/>
        <path d="M38 24 V101 M56 24 V101"/>
        <path d="M47 24 C40 6 24 2 22 12 C20 20 34 24 47 24 C60 24 74 20 72 12 C70 2 54 6 47 24 Z"/>
      </g>
    </svg>
    <p class="comp-title">COMPENSATION</p>
    <p class="comp-upto">UP<br>TO</p>
    <p class="comp-amount">$140</p>
  </footer>
</main>
</body>
</html>
```